Corvana Tongue Works, LLC

We need a business card that includes information about our business and conveys a reliable business that provides document translation services and interpreters for a variety of corporate and individual clients. We want to come across as professional, reliable, yet approachable. It should include the following on one side:

ESL / ENL Language Classes, Private Lessons, and Online Tutors
PLEXA Training and Testing
Translating & Interpreting Services
Contact us about Over-the-Phone Interpreting in over 200 languages
24/7/365
www.corvanatongue.example

The other side should include (555) 481-3062

Rhoda Pelling, President
482 Garnet Ave., Ste. 219
Indianapolis, IN 40917

Please add USA as part of the address. Also, please add rmpelling@corvanatongueworks.example as the e-mail address. Thank you.

Target Market(s)

Business professionals, their families, the international community

Industry/Entity Type

Business

Contact Information for Business Card

24/7/365
www.corvanatongue.example

(555) 481-3062

Rhoda Pelling, President
482 Garnet Ave., Ste. 219
Indianapolis, IN 40917
USA

Font styles to use
Sans Serif

Colors

Designer to choose colors to be used in the design.

Requirements
Must have
• See project description
• e-mail address and web address
• Phone number
Nice to have
• a globe
• physical address
Should not have
• Should not have the same color scheme as other agencies in our market in Indiana unless it is blue and black. No purple or yellow.

```html
<!DOCTYPE html>
<html lang="en">
<head>
<meta charset="utf-8">
<title>Corvana Tongue Works – Business Card</title>
<link href="https://fonts.googleapis.com/css2?family=Work+Sans:wght@400;500&display=swap" rel="stylesheet">
<style>
  :root {
    --brand-blue: #2a9ad8;
    --ink: #1e1e1e;
    --paper: #ffffff;
    --stage: #4b4641;
  }
  * { box-sizing: border-box; margin: 0; padding: 0; }
  html, body { width: 1200px; height: 930px; overflow: hidden; }
  body {
    background: var(--stage);
    font-family: "Work Sans", Arial, sans-serif;
    position: relative;
  }
  .card {
    position: absolute;
    width: 560px;
    height: 320px;
    border-radius: 18px;
    overflow: hidden;
  }

  /* Front: services side */
  .card-front {
    left: 70px; top: 110px;
    background: var(--brand-blue);
    color: var(--paper);
    text-align: center;
    padding: 30px 36px 0;
  }
  .brand-lockup {
    display: flex;
    align-items: center;
    justify-content: center;
    gap: 14px;
    margin-bottom: 16px;
  }
  .brand-dot {
    width: 74px; height: 74px;
    border-radius: 50%;
    border: 3px solid var(--paper);
    flex: none;
  }
  .brand-name {
    text-align: left;
    font-weight: 400;
    font-size: 27px;
    line-height: 1.02;
    color: var(--paper);
  }
  .services {
    font-size: 14px;
    line-height: 1.35;
    font-weight: 500;
  }
  .rule {
    border: 0;
    border-top: 1px solid rgba(255,255,255,.85);
    width: 440px;
    margin: 12px auto;
  }
  .callout { font-size: 14px; line-height: 1.35; font-weight: 500; }

  /* Back: contact side */
  .card-back {
    left: 570px; top: 500px;
    background: var(--paper);
    color: var(--ink);
    display: flex;
    align-items: center;
  }
  .mark-area {
    width: 210px;
    flex: none;
    display: flex;
    flex-direction: column;
    align-items: center;
    gap: 12px;
  }
  .mark-circle {
    width: 124px; height: 124px;
    border-radius: 50%;
    background: var(--brand-blue);
  }
  .mark-name { font-size: 14px; color: var(--brand-blue); font-weight: 400; }
  .divider {
    width: 1.5px; height: 170px;
    background: var(--brand-blue);
    margin-right: 26px;
    flex: none;
  }
  .contact { font-size: 14px; line-height: 1.4; white-space: nowrap; }
  .person-name {
    color: var(--brand-blue);
    font-size: 27px;
    font-weight: 400;
    letter-spacing: .3px;
    line-height: 1.1;
  }
  .person-title { margin-bottom: 10px; }
  .address { margin-bottom: 8px; }
  .contact-line { display: flex; align-items: center; gap: 7px; }
  .contact-line svg { width: 11px; height: 11px; flex: none; }
</style>
</head>
<body>

<section class="card card-front">
  <div class="brand-lockup">
    <span class="brand-dot"></span>
    <div class="brand-name">Corvana<br>Tongue<br>Works LLC</div>
  </div>
  <p class="services">
    ESL / ENL Language Classes, Private Lessons, and Online Tutors<br>
    PLEXA Training and Testing<br>
    Translating &amp; Interpreting Services
  </p>
  <hr class="rule">
  <p class="callout">
    Contact us about Over-the-Phone Interpreting in over 200 languages<br>
    24/7/365<br>
    www.corvanatongue.example
  </p>
</section>

<section class="card card-back">
  <div class="mark-area">
    <span class="mark-circle"></span>
    <span class="mark-name">Corvana Tongue Works</span>
  </div>
  <span class="divider"></span>
  <div class="contact">
    <h1 class="person-name">RHODA PELLING</h1>
    <p class="person-title">President</p>
    <p class="address">482 Garnet Ave., Ste. 219<br>Indianapolis, IN 40917 USA</p>
    <p class="contact-line">
      <svg viewBox="0 0 12 12" aria-hidden="true"><path d="M2.5 1l2 2.3-1 1.3c.8 1.6 1.9 2.7 3.4 3.4l1.3-1 2.3 2-1.2 1.8C5.5 10.5 1.5 6.5 .9 2.2z" fill="var(--brand-blue)"/></svg>
      (555) 481-3062
    </p>
    <p class="contact-line">
      <svg viewBox="0 0 12 12" aria-hidden="true"><rect x="1" y="2.5" width="10" height="7" fill="none" stroke="var(--brand-blue)" stroke-width="1.2"/><path d="M1 2.8l5 3.8 5-3.8" fill="none" stroke="var(--brand-blue)" stroke-width="1.2"/></svg>
      rmpelling@corvanatongueworks.example
    </p>
    <p class="contact-line">
      <svg viewBox="0 0 12 12" aria-hidden="true"><circle cx="6" cy="6" r="5" fill="none" stroke="var(--brand-blue)" stroke-width="1.1"/><ellipse cx="6" cy="6" rx="2.2" ry="5" fill="none" stroke="var(--brand-blue)" stroke-width="1"/><path d="M1 6h10" stroke="var(--brand-blue)" stroke-width="1"/></svg>
      www.corvanatongue.example
    </p>
  </div>
</section>

</body>
</html>
```